A Modern & Sleek "Coming Soon" Page for an A.I Recruiting App

For the “Coming Soon” website, a simple background with no people in it. I've attached an A.I image of what the page should generally look like.

- A single mobile phone as the main focus where the user actually clicks on the, “notify me” button (after entering their email address).
- In the background where the pillars/columns are seen in the example, should be subtle pad locks that are in their opened position with a key inside the lock. I've attached images to try to illustrate this idea, but they are far away in style from what I'm looking for.

SLOGAN: Unlocking the power of meaningful connections
LOGO/TITLE: Should be the name as shown in image with only the name "KelvoLink" on it
COLORS: Purplish/blue hues. Should not be too feminine
NOTE: The user should only click once when signing up/entering their email.

Product: A recruiting platform that matches employers/employees with A.I. and prioritizing cultural fit/values system before skills. The industry we are tackling first is the caregiving industry (nannies, tutors, elderly). All users will be background screened and that info lives on the blockchain. All users will have the option to review and be reviewed/rated.

```html
<!DOCTYPE html>
<html lang="en">
<head>
<meta charset="utf-8">
<title>KelvoLink — Coming Soon</title>
<link rel="stylesheet" href="https://fonts.googleapis.com/css2?family=Roboto:wght@300;400&family=Mulish:wght@500;600;700&display=swap">
<style>
  :root {
    --night: #0b0920;
    --deep-purple: #24124a;
    --violet: #3d2472;
    --teal-glow: #3f93ad;
    --blue-glow: #3b64a8;
    --white: #ffffff;
    --phone-frame: #0e1824;
    --phone-edge: #2c4658;
    --screen-top: #2fb4e0;
    --screen-bottom: #9ff2fb;
    --screen-ink: #102033;
    --button: #4b2a98;
  }
  * { margin: 0; padding: 0; box-sizing: border-box; }
  html, body { width: 1200px; height: 667px; overflow: hidden; background: var(--night); }

  .page {
    position: relative;
    width: 1200px;
    height: 667px;
    overflow: hidden;
    font-family: "Roboto", sans-serif;
    color: var(--white);
    background:
      radial-gradient(ellipse 520px 260px at 230px 520px, rgba(63,147,173,0.75), transparent 70%),
      radial-gradient(ellipse 700px 200px at 560px 620px, rgba(70,150,190,0.45), transparent 70%),
      radial-gradient(ellipse 420px 300px at 1150px 620px, rgba(59,100,168,0.7), transparent 70%),
      radial-gradient(ellipse 380px 300px at 1180px 240px, rgba(90,50,150,0.6), transparent 70%),
      linear-gradient(160deg, #0c1a2c 0%, var(--night) 35%, var(--deep-purple) 75%, var(--violet) 100%);
  }

  .wordmark {
    position: absolute;
    top: 58px;
    left: 0;
    width: 1200px;
    text-align: center;
    font-family: "Roboto", sans-serif;
    font-weight: 300;
    font-size: 80px;
    letter-spacing: 16px;
    text-transform: uppercase;
    color: var(--white);
    line-height: 1;
    padding-left: 16px;
  }

  .slogan {
    position: absolute;
    left: 559px;
    top: 296px;
    width: 500px;
    font-weight: 400;
    font-size: 29px;
    line-height: 60px;
    color: var(--white);
  }

  .phone {
    position: absolute;
    left: 128px;
    top: 142px;
    width: 272px;
    height: 494px;
    transform: rotate(-5deg);
    border-radius: 40px;
    background: var(--phone-frame);
    border: 3px solid var(--phone-edge);
    padding: 10px;
    box-shadow: 10px 14px 30px rgba(0,0,0,0.5);
  }
  .phone-screen {
    position: relative;
    width: 100%;
    height: 100%;
    border-radius: 31px;
    background: linear-gradient(180deg, var(--screen-top) 0%, var(--screen-bottom) 100%);
    text-align: center;
    font-family: "Mulish", sans-serif;
    color: var(--screen-ink);
    overflow: hidden;
  }
  .phone-notch {
    position: absolute;
    top: 0;
    left: 50%;
    width: 124px;
    height: 22px;
    transform: translateX(-50%);
    background: var(--phone-frame);
    border-radius: 0 0 16px 16px;
  }
  .screen-wordmark {
    padding-top: 118px;
    font-family: "Roboto", sans-serif;
    font-weight: 300;
    font-size: 21px;
    letter-spacing: 2px;
    text-transform: uppercase;
    color: var(--white);
  }
  .screen-teaser {
    margin: 28px auto 0;
    width: 190px;
    font-weight: 600;
    font-size: 12.5px;
    line-height: 25px;
  }
  .screen-invite {
    margin-top: 18px;
    font-weight: 600;
    font-size: 12.5px;
    line-height: 25px;
  }
  .signup { margin-top: 26px; }
  .email-field {
    display: block;
    margin: 0 auto;
    width: 140px;
    height: 36px;
    border: none;
    border-radius: 18px;
    background: var(--white);
    font-family: "Mulish", sans-serif;
    font-weight: 600;
    font-size: 8.5px;
    padding-left: 14px;
    color: var(--screen-ink);
  }
  .email-field::placeholder { color: var(--screen-ink); text-transform: uppercase; }
  .notify-button {
    display: block;
    margin: 14px auto 0;
    width: 138px;
    height: 36px;
    border: none;
    border-radius: 18px;
    background: var(--button);
    color: var(--white);
    font-family: "Mulish", sans-serif;
    font-weight: 700;
    font-size: 12px;
    text-transform: uppercase;
    cursor: pointer;
  }
</style>
</head>
<body>
  <main class="page">
    <h1 class="wordmark">KelvoLink</h1>

    <div class="phone">
      <div class="phone-screen">
        <div class="phone-notch"></div>
        <div class="screen-wordmark">KelvoLink</div>
        <p class="screen-teaser">Our tribe council is masterminding something legendary</p>
        <p class="screen-invite">Stay Connected<br>On Our Journey to Compatibility</p>
        <form class="signup" action="#">
          <input class="email-field" type="email" placeholder="Enter email here" aria-label="Email address">
          <button class="notify-button" type="submit">Notify me</button>
        </form>
      </div>
    </div>

    <p class="slogan">Unlocking the Power Of Meaningful Connections</p>
  </main>
</body>
</html>
```